New Business Card Design

We need a business card design for a new company based in Sydney called "Haven and Hue". This is an online buisness which will have an online store providing imported homewares.
We are looking for something that is different, perhaps even in shape and using the logo that was designed by Pixel Harbor.

Attached document is a basic example I want to see more creative versions.

Target Market(s)

Homewares, Interior Design

Industry/Entity Type

Business

Contact Information for Business Card

Company Logo
Company Name
Industry area
Name
Position
Phone
Email
Website
Motto

Requirements
Must have
• Logo
Nice to have
• Social website logos - Chatterloop, Glimmoraly, Quibbly, Boardlyne, Veltrix+

```html
<!DOCTYPE html>
<html lang="en">
<head>
<meta charset="utf-8">
<title>Haven and Hue — Business Card</title>
<link rel="stylesheet" href="https://fonts.googleapis.com/css2?family=Exo+2:wght@400;500&display=swap">
<style>
  :root {
    --backdrop: #cfcfcf;
    --card-black: #0c0c0c;
    --card-white: #ffffff;
    --gold: #b8862e;
    --gold-light: #e0b35a;
    --text-light: #f2f2f2;
    --text-dark: #0c0c0c;
  }
  * { box-sizing: border-box; margin: 0; padding: 0; }
  html, body {
    width: 1200px; height: 1000px; overflow: hidden;
    background: var(--backdrop);
    font-family: "Exo 2", sans-serif;
  }
  .canvas { position: relative; width: 1200px; height: 1000px; }
  .card {
    position: absolute; left: 220px; width: 760px; height: 440px;
    border-radius: 22px; overflow: hidden;
    box-shadow: 0 6px 18px rgba(0,0,0,0.25);
  }
  .card--front { top: 40px; background: var(--card-black); }
  .card--back { top: 520px; background: var(--card-white); }
  .card svg { display: block; width: 100%; height: 100%; }
  .brand-name { font-family: "Exo 2", sans-serif; font-weight: 500; }
  .brand-name--light { fill: var(--text-light); }
  .brand-name--dark { fill: var(--text-dark); }
  .social-name { font-family: "Exo 2", sans-serif; font-weight: 500; font-size: 10px; fill: var(--text-dark); }
  .person-name { font-family: "Exo 2", sans-serif; font-weight: 400; font-size: 28px; fill: var(--gold); }
  .person-role { font-family: "Exo 2", sans-serif; font-weight: 400; font-size: 20px; fill: var(--text-light); }
  .contact-line { font-family: "Exo 2", sans-serif; font-weight: 400; font-size: 17px; fill: var(--text-light); }
  .icon { fill: none; stroke: var(--text-light); stroke-width: 1.6; }
</style>
</head>
<body>
<main class="canvas">

  <section class="card card--front" aria-label="Card front">
    <svg viewBox="0 0 760 440" xmlns="http://www.w3.org/2000/svg">
      <text class="brand-name brand-name--light" x="380" y="234" font-size="44" text-anchor="middle">Haven and Hue</text>
    </svg>
  </section>

  <section class="card card--back" aria-label="Card back">
    <svg viewBox="0 0 760 440" xmlns="http://www.w3.org/2000/svg">
      <defs>
        <linearGradient id="goldSweep" x1="0" y1="0" x2="1" y2="0">
          <stop offset="0" stop-color="var(--gold)"/>
          <stop offset="0.5" stop-color="var(--gold-light)"/>
          <stop offset="1" stop-color="var(--gold)"/>
        </linearGradient>
        <linearGradient id="dividerFade" x1="0" y1="0" x2="0" y2="1">
          <stop offset="0" stop-color="#fff" stop-opacity="0"/>
          <stop offset="0.5" stop-color="#fff" stop-opacity="0.8"/>
          <stop offset="1" stop-color="#fff" stop-opacity="0"/>
        </linearGradient>
      </defs>

      <path class="gold-band" d="M0,322 C200,322 330,288 430,208 C520,138 600,108 760,103 L760,118 C600,122 520,152 430,222 C330,302 200,336 0,336 Z" fill="url(#goldSweep)"/>
      <path class="dark-field" d="M0,338 C200,338 330,304 430,224 C520,154 600,124 760,119 L760,440 L0,440 Z" fill="var(--card-black)"/>

      <text class="brand-name brand-name--dark" x="205" y="170" font-size="30" text-anchor="middle">Haven and Hue</text>

      <text class="social-name" x="730" y="42" text-anchor="end">Chatterloop · Quibbly · Glimmoraly · Boardlyne · Veltrix+</text>

      <g class="person">
        <text class="person-name" x="110" y="385">Marcus Ellery</text>
        <text class="person-role" x="190" y="412">Director</text>
      </g>

      <rect class="divider" x="428" y="280" width="2" height="130" fill="url(#dividerFade)"/>

      <g class="contact">
        <rect class="icon" x="462" y="276" width="11" height="18" rx="2"/>
        <text class="contact-line" x="488" y="291">0798 456 213</text>
        <rect class="icon" x="460" y="310" width="16" height="12"/>
        <path class="icon" d="M460,310 L468,317 L476,310"/>
        <text class="contact-line" x="488" y="322">me@havenandhue.com.au</text>
        <circle class="icon" cx="468" cy="346" r="8"/>
        <path class="icon" d="M460,346 H476 M468,338 V354"/>
        <text class="contact-line" x="488" y="352">www.havenandhue.com.au</text>
      </g>
    </svg>
  </section>

</main>
</body>
</html>
```